7K packaging design

We are a wholesaler for Automotive Spare Parts in Jordan and Iraq market and we needs to import spare parts from China under our company private brand "7K"
The 7K brand’s product lines include Filtration, Braking Systems, Wheels, Wheel Bolts & Nuts, Shock Absorbers, Sensors, Cooling Systems, Axles and more.
The aim of the project is to unify the brand packaging across all the product lines , we will start by the brake pads then based on the approved design we will do the other products

Target Market(s)

Jordan , Iraq Market

Industry/Entity Type

Automotive spare parts

Requirements
Must have
• Name of the product :Ceramic brake pads specs : Superior stopping power Noise suppression Low Dust Technology Made in china
Nice to have
• Brake pad outline image on the box
Should not have
• Blue color

```html
<!DOCTYPE html>
<html lang="en">
<head>
<meta charset="utf-8">
<title>7K Ceramic Brake Pads – Box Front</title>
<link rel="stylesheet" href="https://fonts.googleapis.com/css2?family=Anton&family=Open+Sans:wght@400;600&display=swap">
<style>
  :root {
    --canvas: #f4f4f4;
    --red: #e3141c;
    --red-deep: #b80d14;
    --black: #161616;
    --charcoal: #2b2b2b;
    --gold: #c9a24a;
    --white: #ffffff;
    --grey: #8c8c8c;
  }
  * { margin: 0; padding: 0; box-sizing: border-box; }
  html, body { width: 1200px; height: 884px; overflow: hidden; background: var(--canvas); }
  .box-front {
    position: absolute; left: 50px; top: 137px; width: 1100px; height: 610px;
    overflow: hidden; background: var(--charcoal);
    font-family: "Open Sans", sans-serif;
  }
  .panel-split { position: absolute; inset: 0; }
  .car-visual {
    position: absolute; left: 250px; top: 250px; width: 420px; height: 170px;
    border-radius: 90px 120px 30px 30px;
    background: radial-gradient(ellipse at 60% 50%, rgba(255,140,60,.55), rgba(255,90,40,0) 70%);
  }
  .headline { position: absolute; left: 38px; top: 64px; font-family: "Anton", sans-serif; line-height: .98; }
  .headline .line-ceramic { display: block; font-size: 94px; color: var(--white); letter-spacing: 1px; }
  .headline .line-pads { display: block; font-size: 94px; color: var(--black); letter-spacing: 1px; }
  .rule { position: absolute; left: 38px; top: 305px; width: 262px; height: 2px;
    background: linear-gradient(90deg, var(--white), rgba(255,255,255,0)); transform: rotate(-1.5deg); }
  .specs { position: absolute; left: 38px; top: 338px; list-style: none; }
  .specs li { font-size: 22px; color: var(--white); margin-bottom: 17px; display: flex; align-items: center; }
  .specs li::before { content: ""; width: 11px; height: 11px; border-radius: 50%;
    border: 3px solid rgba(255,255,255,.7); margin-right: 12px; }
  .features { position: absolute; left: 36px; top: 478px; display: flex; gap: 22px; }
  .feature { width: 54px; text-align: center; color: var(--white); font-size: 17px; line-height: 1.1; }
  .feature svg { display: block; margin: 0 auto 6px; }
  .brand-mark { position: absolute; right: 48px; top: 42px; display: flex; align-items: center; gap: 12px; }
  .brand-mark .dot { width: 22px; height: 22px; border-radius: 50%; background: var(--red); }
  .brand-mark .name { font-family: "Anton", sans-serif; font-size: 84px; color: var(--white); line-height: 1; }
  .pad-visual {
    position: absolute; left: 694px; top: 228px; width: 364px; height: 320px;
    border-radius: 40px 40px 20px 20px;
    background: linear-gradient(160deg, #3a3a3a 0%, #1c1c1c 45%, #8a8a8a 75%, #5a5a5a 100%);
  }
  .quality-badge { position: absolute; left: 516px; top: 482px; }
  .made-in { position: absolute; right: 28px; bottom: 14px; font-size: 13px; color: var(--grey); letter-spacing: 1px; }
</style>
</head>
<body>
<main class="box-front">
  <svg class="panel-split" width="1100" height="610" viewBox="0 0 1100 610" aria-hidden="true">
    <defs>
      <linearGradient id="redFace" x1="0" y1="0" x2="1" y2="1">
        <stop offset="0" stop-color="#ee1d24"/>
        <stop offset="1" stop-color="#c00f16"/>
      </linearGradient>
      <linearGradient id="darkFace" x1="0" y1="0" x2="0" y2="1">
        <stop offset="0" stop-color="#333"/>
        <stop offset="1" stop-color="#1e1e1e"/>
      </linearGradient>
    </defs>
    <rect width="1100" height="610" fill="url(#darkFace)"/>
    <path d="M0 0 H778 C770 140 700 210 640 300 C580 390 500 460 470 610 H0 Z" fill="url(#redFace)"/>
    <path d="M778 0 C770 140 700 210 640 300 C580 390 500 460 470 610" fill="none" stroke="var(--gold)" stroke-width="3"/>
  </svg>

  <div class="car-visual" role="img" aria-label="Soft glowing sports car illustration"></div>

  <h1 class="headline">
    <span class="line-ceramic">CERAMIC</span>
    <span class="line-pads">BRAKE PADS</span>
  </h1>
  <div class="rule"></div>

  <ul class="specs">
    <li>Superior Stopping Power</li>
    <li>Noise Suppression</li>
    <li>Low Dust Technology</li>
  </ul>

  <div class="features">
    <div class="feature">
      <svg width="52" height="52" viewBox="0 0 52 52" aria-hidden="true"><circle cx="26" cy="26" r="23" fill="none" stroke="#111" stroke-width="3"/><rect x="13" y="22" width="12" height="8" rx="4" fill="none" stroke="#111" stroke-width="2.5"/><rect x="27" y="22" width="12" height="8" rx="4" fill="none" stroke="#111" stroke-width="2.5"/></svg>
      Super Strong
    </div>
    <div class="feature">
      <svg width="52" height="52" viewBox="0 0 52 52" aria-hidden="true"><circle cx="26" cy="26" r="23" fill="none" stroke="#111" stroke-width="3"/><circle cx="26" cy="26" r="9" fill="none" stroke="#111" stroke-width="3"/><path d="M16 36 L36 16" stroke="#111" stroke-width="2.5"/></svg>
      Rust Proof
    </div>
    <div class="feature">
      <svg width="52" height="52" viewBox="0 0 52 52" aria-hidden="true"><circle cx="26" cy="26" r="23" fill="none" stroke="#111" stroke-width="3"/><circle cx="26" cy="22" r="8" fill="none" stroke="#111" stroke-width="2.5"/><path d="M21 29 L18 39 L23 36 M31 29 L34 39 L29 36" fill="none" stroke="#111" stroke-width="2.5"/></svg>
      100% Genuine
    </div>
    <div class="feature">
      <svg width="52" height="52" viewBox="0 0 52 52" aria-hidden="true"><circle cx="26" cy="26" r="23" fill="none" stroke="#111" stroke-width="3"/><path d="M17 22 H22 L29 16 V36 L22 30 H17 Z" fill="#111"/><path d="M14 14 L38 38" stroke="#111" stroke-width="2.5"/></svg>
      Ultra Quiet
    </div>
  </div>

  <div class="brand-mark">
    <span class="dot"></span>
    <span class="name">7K</span>
  </div>

  <div class="pad-visual" role="img" aria-label="Ceramic brake pad pair with backing plate and friction surface"></div>

  <svg class="quality-badge" width="96" height="106" viewBox="0 0 96 106" aria-hidden="true">
    <circle cx="48" cy="53" r="46" fill="var(--gold)"/>
    <circle cx="48" cy="53" r="36" fill="#1a1a1a"/>
  </svg>

  <p class="made-in">MADE IN CHINA</p>
</main>
</body>
</html>
```